Telecommunications/Power civil contractor needs business card design

Were a new telecommunications/power underground civil contractor that is looking for a new business card design. Our company colours are silver or grey and orange. Feel free to use the white background logo or the black background logo.

Target Market(s)

Local contractors, utility companies, private sector mining/energy companies, developers.

Industry/Entity Type

Telecommunications

Contact Information for Business Card

Each card will need the following info:
Persons name:
Title:
E-mail:
Phone number:
Shop Address:
Mailing Address:

Requirements
Must have
• Each card will need the following info:
• Persons name:
• Title:
• E-mail:
• Phone number:
• Shop Address:
• Mailing Address:

```html
<!DOCTYPE html>
<html lang="en">
<head>
<meta charset="utf-8">
<title>Kestrel Line Contracting Inc — Business Card</title>
<link href="https://fonts.googleapis.com/css2?family=Open+Sans:wght@400;600;700&display=swap" rel="stylesheet">
<style>
  :root {
    --backdrop: #2b2b2c;
    --white: #ffffff;
    --graphite: #58585a;
    --orange: #f15a22;
    --black: #141414;
    --silver: #8a8a8c;
    --text-light: #ececec;
  }
  * { margin: 0; padding: 0; box-sizing: border-box; }
  html, body {
    width: 1200px; height: 716px; overflow: hidden;
    background: var(--backdrop);
    font-family: "Open Sans", Arial, sans-serif;
  }
  .canvas {
    position: relative; width: 1200px; height: 716px;
  }
  .card {
    position: absolute; top: 215px;
    width: 500px; height: 286px;
    overflow: hidden;
    box-shadow: 0 10px 28px rgba(0,0,0,.45);
  }
  .card-front { left: 60px; background: var(--graphite); }
  .card-back { left: 640px; background: var(--black); }

  .front-brand {
    position: absolute; left: 0; top: 0; bottom: 0; width: 190px;
    background: var(--white);
    display: flex; flex-direction: column; align-items: center; justify-content: center;
    gap: 10px; padding-bottom: 40px;
  }
  .brand-mark {
    width: 46px; height: 46px; border-radius: 50%;
    border: 4px solid var(--orange);
  }
  .brand-name {
    color: var(--orange); font-weight: 700; font-size: 15px;
    text-align: center; line-height: 1.15; letter-spacing: .5px;
    text-transform: uppercase;
  }
  .name-band {
    position: absolute; left: 190px; right: 0; top: 34px; height: 50px;
    background: var(--orange); color: var(--white);
    padding: 7px 0 0 22px;
  }
  .person-name { font-weight: 700; font-size: 14px; line-height: 1.3; }
  .person-title { font-size: 13px; line-height: 1.3; }

  .contact {
    position: absolute; left: 212px; top: 150px;
    color: var(--text-light); font-size: 12.5px; line-height: 1.5;
  }
  .contact-line { display: flex; align-items: center; gap: 8px; }
  .contact-line svg { flex: none; }

  .back-brand {
    position: absolute; inset: 0;
    display: flex; flex-direction: column; align-items: center; justify-content: center;
    gap: 12px;
  }
  .back-brand .brand-mark { width: 62px; height: 62px; border-width: 5px; }
  .back-brand .brand-name { font-size: 22px; }
</style>
</head>
<body>
<main class="canvas">
  <section class="card card-front" aria-label="Business card front">
    <div class="front-brand">
      <span class="brand-mark"></span>
      <span class="brand-name">Kestrel Line<br>Contracting Inc</span>
    </div>
    <div class="name-band">
      <p class="person-name">Dorian Vale</p>
      <p class="person-title">Managing Director</p>
    </div>
    <div class="contact">
      <p>Kestrel Line Contracting Inc</p>
      <p>N. 8 Harbor Lane,</p>
      <p>Suite 210, Tacoma, WA 55555</p>
      <p class="contact-line">
        <svg width="11" height="11" viewBox="0 0 12 12" aria-hidden="true"><path fill="#f15a22" d="M2.4 1 4.2 0.6 5.4 3.2 4.2 4.3C4.9 5.8 6.2 7.1 7.7 7.8L8.8 6.6 11.4 7.8 11 9.6C10.8 10.5 10 11.1 9.1 11 4.6 10.5 1.5 7.4 1 2.9 .9 2 1.5 1.2 2.4 1Z"/></svg>
        555.010.2040
      </p>
      <p class="contact-line">
        <svg width="11" height="11" viewBox="0 0 12 12" aria-hidden="true"><rect x="0.5" y="2" width="11" height="8" rx="1" fill="#f15a22"/><path d="M1 2.8 6 6.6 11 2.8" stroke="#58585a" stroke-width="1.1" fill="none"/></svg>
        info@kestrellineinc.com
      </p>
    </div>
  </section>

  <section class="card card-back" aria-label="Business card back">
    <div class="back-brand">
      <span class="brand-mark"></span>
      <span class="brand-name">Kestrel Line<br>Contracting Inc</span>
    </div>
  </section>
</main>
</body>
</html>
```